Velmora Nightclub Flyer (Updated)

Flyer for facebook, square is fine, or rectangular. Here is the text:
VELMORA
Nightclub + Lounge
presents

B2B THURSDAY
Nov 29 2018

CLUB FLOOR:
ROLF B2B GARTH
BENEDICT SALVORTE

LOUNGE:
TOBY B2B MY COUSIN
THUNDER REGGIE

Powered by KELP Acoustics
4726 8th Avenue 21+ 9pm-2am
velmorakestrel.com for VIP booth inquiries

Target Market(s)

Nightclub

Industry/Entity Type

Night Club

Font styles to use
Sans Serif

Colors

Designer to choose colors to be used in the design.

Requirements
Must have
• All the text listed, and plz keep the theme of the attached files. We want to stay consistent with the Velmora brand
Nice to have
• Try to stay with the theme from the attachments
Should not have
• Dont' stray to far from the general theme we have from the attachments

```html
<!DOCTYPE html>
<html lang="en">
<head>
<meta charset="utf-8">
<title>Velmora Nightclub + Lounge — B2B Thursday</title>
<link rel="stylesheet" href="https://fonts.googleapis.com/css2?family=Bodoni+Moda:wght@400;500&family=Montserrat:wght@300;400&family=Oswald:wght@600&display=swap">
<style>
  :root {
    --backdrop: #e9e9e9;
    --paper: #ffffff;
    --ink: #231f20;
    --gold: #c9995a;
    --gold-light: #e6c48e;
    --muted: #7a7a7a;
    --rule: #eeeeee;
  }
  html, body {
    margin: 0;
    padding: 0;
    width: 1200px;
    height: 1162px;
    overflow: hidden;
    background: var(--backdrop);
  }
  .flyer {
    position: absolute;
    left: 304px;
    top: 285px;
    width: 593px;
    height: 593px;
    background: var(--paper);
    overflow: hidden;
    color: var(--ink);
  }
  .brand-name {
    position: absolute;
    left: 0;
    right: 0;
    top: 76px;
    margin: 0;
    text-align: center;
    font-family: "Bodoni Moda", serif;
    font-weight: 400;
    font-size: 66px;
    line-height: 1;
    letter-spacing: 2px;
    color: var(--ink);
  }
  .brand-tagline {
    position: absolute;
    left: 0;
    right: 0;
    top: 160px;
    margin: 0;
    text-align: center;
    font-family: "Montserrat", sans-serif;
    font-weight: 400;
    font-size: 12.5px;
    line-height: 15px;
    letter-spacing: 3.6px;
    color: var(--ink);
  }
  .event-date {
    position: absolute;
    left: 296px;
    top: 264px;
    width: 55px;
    height: 23px;
    border: 1px solid var(--gold);
    font-family: "Bodoni Moda", serif;
    font-size: 15px;
    line-height: 23px;
    text-align: center;
    color: var(--gold);
  }
  .event-title {
    position: absolute;
    left: 361px;
    top: 265px;
    margin: 0;
    font-family: "Bodoni Moda", serif;
    font-weight: 500;
    font-size: 15px;
    letter-spacing: 0.6px;
    line-height: 20px;
    color: var(--ink);
  }
  .title-rule {
    position: absolute;
    left: 361px;
    top: 284px;
    width: 170px;
    height: 8px;
  }
  .lineup {
    position: absolute;
    left: 0;
    width: 593px;
    margin: 0;
  }
  .lineup-floor { top: 315px; }
  .lineup-lounge { top: 366px; }
  .room-label {
    position: absolute;
    right: 240px;
    top: 1px;
    font-family: "Oswald", sans-serif;
    font-weight: 600;
    font-size: 8px;
    letter-spacing: 1px;
    color: var(--ink);
  }
  .lineup-floor .room-label { right: 246px; }
  .artists {
    position: absolute;
    left: 361px;
    top: 0;
    margin: 0;
    padding: 0;
    list-style: none;
    font-family: "Montserrat", sans-serif;
    font-size: 9.6px;
    line-height: 13px;
    letter-spacing: 0.2px;
    color: var(--ink);
  }
  .venue-details {
    position: absolute;
    left: 370px;
    top: 478px;
    width: 158px;
    height: 71px;
    border-top: 1px solid var(--rule);
    border-bottom: 1px solid var(--rule);
    box-sizing: border-box;
    padding-top: 11px;
    font-family: "Montserrat", sans-serif;
    font-weight: 300;
    font-size: 9.6px;
    line-height: 10.5px;
    color: var(--muted);
    text-transform: uppercase;
  }
  .venue-details p { margin: 0 0 5px; }
  .venue-details sup { font-size: 6px; line-height: 0; }
  .ornament-area {
    position: absolute;
    left: 0;
    top: 288px;
    width: 252px;
    height: 305px;
  }
</style>
</head>
<body>
  <main class="flyer">
    <h1 class="brand-name">VELMORA</h1>
    <p class="brand-tagline">NIGHTCLUB + LOUNGE<br>PRESENTS</p>

    <div class="event-date">NOV 29</div>
    <h2 class="event-title">B2B Thursday</h2>
    <svg class="title-rule" viewBox="0 0 170 8" aria-hidden="true">
      <line x1="0" y1="4" x2="158" y2="4" stroke="#c9995a" stroke-width="0.8"/>
      <circle cx="164" cy="4" r="2.4" fill="none" stroke="#c9995a" stroke-width="0.8"/>
    </svg>

    <section class="lineup lineup-floor">
      <span class="room-label">CLUB FLOOR:</span>
      <ul class="artists">
        <li>ROLF B2B GARTH</li>
        <li>BENEDICT SALVORTE</li>
      </ul>
    </section>

    <section class="lineup lineup-lounge">
      <span class="room-label">LOUNGE:</span>
      <ul class="artists">
        <li>TOBY B2B MY COUSIN</li>
        <li>THUNDER REGGIE</li>
      </ul>
    </section>

    <footer class="venue-details">
      <p>Powered by KELP Acoustics<br>4726 8<sup>TH</sup> Avenue 21+ 9pm-2am</p>
      <p>velmorakestrel.com for<br>VIP booth inquiries</p>
    </footer>

    <svg class="ornament-area" viewBox="0 0 252 305" role="img" aria-label="Gold line-art mandala ornament rising from the lower left corner">
      <defs>
        <radialGradient id="goldGlow" cx="0" cy="1" r="1">
          <stop offset="0" stop-color="#c9995a" stop-opacity="0.55"/>
          <stop offset="1" stop-color="#e6c48e" stop-opacity="0.35"/>
        </radialGradient>
      </defs>
      <path d="M0 0 Q120 40 190 150 Q235 220 252 305 L0 305 Z" fill="url(#goldGlow)"/>
    </svg>
  </main>
</body>
</html>
```